Corvane Freight Company Business Card Design

We are a company that delivers natural saltwater (from the ocean) to aquarium companies, restaurants and home marine tanks. I would like a new business card to suit.

Must include Name, company name, abn, contact number and website as well as logo (see attached).

Looking for a design that stands out, has a clean but unique appearance.

Double and single sided entries welcome

Business

• Logo

```html
<!DOCTYPE html>
<html lang="en">
<head>
<meta charset="utf-8">
<title>Corvane Freight Company – Business Card</title>
<link rel="stylesheet" href="https://fonts.googleapis.com/css2?family=Jost:wght@400;500;700&display=swap">
<style>
  :root {
    --backdrop: #1f1f21;
    --card-blue: #2f7cef;
    --ink-white: #ffffff;
    --ink-soft: #e8f1ff;
    --divider: rgba(255,255,255,0.85);
  }
  * { margin: 0; padding: 0; box-sizing: border-box; }
  html, body {
    width: 1200px; height: 1061px; overflow: hidden;
    background: var(--backdrop);
    font-family: "Jost", "Futura", sans-serif;
    color: var(--ink-white);
  }
  .canvas { position: relative; width: 1200px; height: 1061px; }
  .card {
    position: absolute;
    width: 760px; height: 435px;
    border-radius: 30px;
    background: var(--card-blue);
  }
  .card--front { left: 65px; top: 82px; }
  .card--back  { left: 350px; top: 554px; }

  .brand {
    position: absolute; left: 0; right: 0;
    display: flex; align-items: center; justify-content: center; gap: 16px;
    font-weight: 700; color: var(--ink-white);
    letter-spacing: 0.5px;
  }
  .brand__dot {
    width: 22px; height: 22px; border-radius: 50%;
    background: var(--ink-white);
  }
  .card--front .brand { top: 105px; font-size: 54px; }
  .card--back .brand  { top: 180px; font-size: 60px; }

  .holder {
    position: absolute; left: 0; right: 0; top: 244px;
    text-align: center; font-size: 25px;
  }
  .holder__name { font-weight: 700; }
  .holder__title { font-weight: 400; font-size: 21px; }

  .contact {
    position: absolute; top: 310px; font-size: 18.5px; line-height: 25px;
    color: var(--ink-soft);
  }
  .contact--address { right: 384px; text-align: right; }
  .contact--address .contact__company { font-size: 20px; }
  .contact--lines { left: 412px; }
  .contact__row { display: flex; align-items: center; gap: 6px; }
  .contact__row svg { width: 15px; height: 15px; flex: none; }
  .contact-divider {
    position: absolute; left: 398px; top: 305px;
    width: 1.5px; height: 88px; background: var(--divider);
  }

  .web {
    position: absolute; left: 0; right: 0; top: 352px;
    text-align: center; font-size: 27px; letter-spacing: 4px;
    color: var(--ink-soft);
  }
</style>
</head>
<body>
<main class="canvas">

  <section class="card card--front" aria-label="Business card front">
    <div class="brand"><span class="brand__dot"></span><span>Corvane Freight</span></div>
    <p class="holder"><span class="holder__name">Your name,</span> <span class="holder__title">Title</span></p>

    <div class="contact contact--address">
      <p class="contact__company">Corvane Freight LLC</p>
      <p>Street Name, City Name</p>
      <p>State, City Zip Code</p>
    </div>
    <span class="contact-divider"></span>
    <div class="contact contact--lines">
      <p class="contact__row">
        <svg viewBox="0 0 16 16" aria-hidden="true"><circle cx="8" cy="8" r="7" fill="none" stroke="#fff" stroke-width="1.3"/><path d="M5.2 4.3l1.3 1.6-.7 1c.5 1.1 1.3 1.9 2.4 2.4l1-.7 1.6 1.3-.8 1.2C7.7 11 5 8.3 4 5.1z" fill="#fff"/></svg>
        <span>123-456-7890</span>
      </p>
      <p class="contact__row">
        <svg viewBox="0 0 16 16" aria-hidden="true"><circle cx="8" cy="8" r="6.5" fill="#fff"/><path d="M1.5 8h13M8 1.5c-2.5 3-2.5 10 0 13M8 1.5c2.5 3 2.5 10 0 13" fill="none" stroke="#2f7cef" stroke-width="1"/></svg>
        <span>www.website.com</span>
      </p>
      <p>ABN : 0123456789</p>
    </div>
  </section>

  <section class="card card--back" aria-label="Business card back">
    <div class="brand"><span class="brand__dot"></span><span>Corvane Freight</span></div>
    <p class="web">www.website.com</p>
  </section>

</main>
</body>
</html>
```